Design 4 pages for an event discovery website

This is a contest for the design of 4 pages for an events discovery website. The feature is part of the new sign-up process.

Please see the attached document for a full scope, mockups and the parent category icons.

Target Market(s)

18-35 Australian event goers

Industry/Entity Type

Events

Number of Pages Required

4 page

```html
<!DOCTYPE html>
<html lang="en">
<head>
<meta charset="utf-8">
<title>Eventora – Sign Up</title>
<link rel="stylesheet" href="https://fonts.googleapis.com/css2?family=Open+Sans:wght@400;600&family=Raleway:wght@300;400;500;600&display=swap">
<style>
  :root {
    --blue-top: #2f7fd0;
    --blue-bottom: #134fa3;
    --blue-deep: #0e3f8a;
    --navy-btn: #0b3a78;
    --orange: #f7931e;
    --heading-blue: #13498f;
    --text-dark: #333333;
    --text-mid: #444444;
    --field-border: #c9c9c9;
    --field-top: #ffffff;
    --field-bottom: #ececec;
    --footer-bg: #efefef;
    --footer-line: #d4d4d4;
    --icon-grey: #6d6d6d;
    --white: #ffffff;
  }
  * { box-sizing: border-box; margin: 0; padding: 0; }
  html, body { width: 1200px; height: 622px; overflow: hidden; background: var(--white); }
  body { position: relative; font-family: "Open Sans", Arial, sans-serif; color: var(--text-dark); }

  .site-header {
    position: absolute; left: 0; top: 0; width: 1200px; height: 96px;
    background: linear-gradient(to bottom, var(--blue-top), var(--blue-bottom));
  }
  .brand {
    position: absolute; left: 141px; top: 20px;
    font-family: "Raleway", Arial, sans-serif; font-weight: 400; font-size: 38px;
    color: var(--white); letter-spacing: 0.5px;
  }
  .nav-link {
    position: absolute; left: 345px; top: 37px;
    font-family: "Raleway", Arial, sans-serif; font-size: 18px; color: var(--white);
  }
  .search {
    position: absolute; left: 688px; top: 37px; width: 196px; height: 29px;
    background: var(--white); border: 2px solid #c7d6ea; border-radius: 15px;
    font-size: 10px; color: #555; padding: 7px 0 0 15px;
  }
  .search svg { position: absolute; right: 11px; top: 6px; }
  .btn-pill {
    position: absolute; top: 37px; height: 28px; border-radius: 14px;
    font-family: "Raleway", Arial, sans-serif; font-weight: 500; font-size: 13px;
    color: var(--white); text-align: center; line-height: 28px;
  }
  .btn-signup { left: 907px; width: 74px; background: var(--navy-btn); }
  .btn-login { left: 987px; width: 74px; top: 36px; background: var(--orange); }

  .page-title {
    position: absolute; left: 141px; top: 138px;
    font-family: "Raleway", Arial, sans-serif; font-weight: 300; font-size: 37px;
    color: var(--heading-blue);
  }
  .field {
    position: absolute; left: 139px; width: 289px; height: 33px;
    background: linear-gradient(to bottom, var(--field-top), var(--field-bottom));
    border: 1px solid var(--field-border);
    font-size: 11.5px; color: var(--text-mid); padding: 9px 0 0 18px;
  }
  .required {
    position: absolute; left: 433px; color: var(--orange); font-size: 14px; font-weight: 600;
  }
  .btn-submit {
    position: absolute; left: 140px; top: 473px; width: 125px; height: 37px;
    background: linear-gradient(to bottom, #1c63b8, var(--blue-deep));
    color: var(--white); font-family: "Raleway", Arial, sans-serif; font-weight: 500;
    font-size: 18px; text-align: center; line-height: 37px; border-radius: 2px;
  }

  .benefits-title {
    position: absolute; left: 580px; top: 168px;
    font-family: "Raleway", Arial, sans-serif; font-weight: 400; font-size: 23px;
    color: var(--text-dark);
  }
  .benefit {
    position: absolute; left: 578px; width: 464px; height: 31px;
    font-size: 12px; color: var(--text-dark); padding-left: 30px; line-height: 20px;
  }
  .benefit svg { position: absolute; left: 2px; top: 1px; }
  .benefit-rule {
    position: absolute; left: 0; bottom: 0; width: 464px; height: 1px;
    background: linear-gradient(to right, #e2e2e2, #e2e2e2 80%, rgba(226,226,226,0));
  }

  .site-footer {
    position: absolute; left: 0; top: 558px; width: 1200px; height: 64px;
    background: var(--footer-bg); border-top: 1px solid var(--footer-line);
  }
  .legal { position: absolute; left: 141px; top: 21px; font-size: 11px; color: var(--text-dark); }
  .social { position: absolute; top: 20px; width: 19px; height: 19px; border-radius: 3px; background: var(--icon-grey); }
  .page-code { position: absolute; left: 1170px; top: 44px; font-size: 10px; color: var(--text-dark); }
</style>
</head>
<body>
  <header class="site-header">
    <div class="brand">Eventora</div>
    <div class="nav-link">Find Events</div>
    <div class="search">Search
      <svg width="14" height="14" viewBox="0 0 14 14" aria-hidden="true">
        <circle cx="5.8" cy="5.8" r="4.3" fill="none" stroke="#8a8a8a" stroke-width="2"/>
        <line x1="9" y1="9" x2="12.6" y2="12.6" stroke="#8a8a8a" stroke-width="2.2" stroke-linecap="round"/>
      </svg>
    </div>
    <div class="btn-pill btn-signup">Sign Up</div>
    <div class="btn-pill btn-login">Log In</div>
  </header>

  <main>
    <h1 class="page-title">Sign Up</h1>
    <div class="field" style="top:198px">Username</div>
    <span class="required" style="top:189px">*</span>
    <div class="field" style="top:236px">Email address</div>
    <span class="required" style="top:228px">*</span>
    <div class="field" style="top:274px;left:140px">Password</div>
    <div class="field" style="top:313px;left:140px">Confirm Password</div>
    <div class="field" style="top:353px;left:140px">First Name</div>
    <div class="field" style="top:391px;left:140px">Last Name</div>
    <div class="field" style="top:430px;left:140px">Date of Birth</div>
    <div class="btn-submit">Sign Up</div>

    <h2 class="benefits-title">Feature Benefits</h2>
    <div class="benefit" style="top:212px"><svg width="18" height="18" viewBox="0 0 18 18" aria-hidden="true"><circle cx="9" cy="9" r="9" fill="#f7931e"/><path d="M4.8 9.2l2.8 2.8 5.6-5.6" fill="none" stroke="#fff" stroke-width="2.2" stroke-linecap="round" stroke-linejoin="round"/></svg>Get personalised event recommendations<span class="benefit-rule"></span></div>
    <div class="benefit" style="top:244px"><svg width="18" height="18" viewBox="0 0 18 18" aria-hidden="true"><circle cx="9" cy="9" r="9" fill="#f7931e"/><path d="M4.8 9.2l2.8 2.8 5.6-5.6" fill="none" stroke="#fff" stroke-width="2.2" stroke-linecap="round" stroke-linejoin="round"/></svg>Get notified about your favourite events - never miss out again<span class="benefit-rule"></span></div>
    <div class="benefit" style="top:276px"><svg width="18" height="18" viewBox="0 0 18 18" aria-hidden="true"><circle cx="9" cy="9" r="9" fill="#f7931e"/><path d="M4.8 9.2l2.8 2.8 5.6-5.6" fill="none" stroke="#fff" stroke-width="2.2" stroke-linecap="round" stroke-linejoin="round"/></svg>Follow all your favourite artists, musicians, teams and players in one place<span class="benefit-rule"></span></div>
    <div class="benefit" style="top:307px"><svg width="18" height="18" viewBox="0 0 18 18" aria-hidden="true"><circle cx="9" cy="9" r="9" fill="#f7931e"/><path d="M4.8 9.2l2.8 2.8 5.6-5.6" fill="none" stroke="#fff" stroke-width="2.2" stroke-linecap="round" stroke-linejoin="round"/></svg>Follow your favourite local venues to know everything happening there<span class="benefit-rule"></span></div>
    <div class="benefit" style="top:339px"><svg width="18" height="18" viewBox="0 0 18 18" aria-hidden="true"><circle cx="9" cy="9" r="9" fill="#f7931e"/><path d="M4.8 9.2l2.8 2.8 5.6-5.6" fill="none" stroke="#fff" stroke-width="2.2" stroke-linecap="round" stroke-linejoin="round"/></svg>Get curated news and feature content on your favourite artists (coming soon)<span class="benefit-rule"></span></div>
    <div class="benefit" style="top:370px"><svg width="18" height="18" viewBox="0 0 18 18" aria-hidden="true"><circle cx="9" cy="9" r="9" fill="#f7931e"/><path d="M4.8 9.2l2.8 2.8 5.6-5.6" fill="none" stroke="#fff" stroke-width="2.2" stroke-linecap="round" stroke-linejoin="round"/></svg>Invite your mates to events via Mateline (ML sign-up only)</div>
  </main>

  <footer class="site-footer">
    <div class="legal">© 2015 Company Name&nbsp; All right reserved&nbsp; Term of Use</div>
    <span class="social" style="left:976px" role="img" aria-label="Social link"></span>
    <span class="social" style="left:1000px" role="img" aria-label="Social link"></span>
    <span class="social" style="left:1024px" role="img" aria-label="Social link"></span>
    <div class="page-code">X14</div>
  </footer>
</body>
</html>
```